Brookmere Osteopathy flyer

I want a clean clear DL flyer (but also want an A4 poster) promoting a new Osteopathic business in a semi rural area in Tasmania (Australia).
It can have pictures like the examples attached to show people what Osteopathy is (its like Chiropractic and physiotherapy).
I am the sole practioner and am male, so any pictures would be best to be a white male if possible.
I've attached some wording, you can use all, or none of it
I don't have a phone number for the business yet
info@brookmereosteopathy.example
www.brookmereosteopathy.example
Target Market(s)
Australians, from tradies, professionals, babies to retired people
Industry/Entity Type
Health
Look and feel

```html
<!DOCTYPE html>
<html lang="en">
<head>
<meta charset="utf-8">
<title>Brookmere Osteopathy – Flyer</title>
<link href="https://fonts.googleapis.com/css2?family=Montserrat:ital,wght@0,500;0,600;0,700;1,400;1,600&family=Playfair+Display:ital,wght@1,600&family=Poppins:wght@400;600&display=swap" rel="stylesheet">
<style>
  :root{
    --mat:#4f4f4f;
    --white:#ffffff;
    --brand-blue:#1a8dd6;
    --spine:#1395d1;
    --orange:#f28a2e;
    --ink:#1f1f1f;
  }
  *{margin:0;padding:0;box-sizing:border-box}
  html,body{width:678px;height:1200px;overflow:hidden;background:var(--mat)}
  .flyer{position:absolute;left:88px;top:68px;width:500px;height:1061px;background:var(--white);overflow:hidden;font-family:"Montserrat",sans-serif}
  .flyer-shapes{position:absolute;inset:0;width:500px;height:1061px}
  .headline{position:absolute;left:281px;top:29px;line-height:1}
  .headline-main{font-weight:700;font-size:28px;color:var(--brand-blue);letter-spacing:-.2px}
  .headline-sub{font-family:"Playfair Display",serif;font-style:italic;font-weight:600;font-size:29px;color:var(--orange);margin-top:2px;letter-spacing:-.5px}
  .intro{position:absolute;left:15px;width:172px;top:587px;text-align:center;font-style:italic;font-weight:400;font-size:15.5px;line-height:22.1px;color:var(--white)}
  .intro strong{color:var(--orange);font-weight:600}
  .reasons-title{position:absolute;left:239px;top:651px;width:360px;transform:translate(-50%,-50%) rotate(-90deg);color:var(--white);font-weight:600;font-size:24px;line-height:30px;text-align:center;white-space:nowrap}
  .condition{position:absolute;width:96px;margin-left:-48px;text-align:center;color:var(--white);font-weight:500;font-size:13px;line-height:16px}
  .call-pill{position:absolute;left:191px;top:940px;width:281px;height:30px;border-radius:15px;background:var(--orange);color:var(--white);font-weight:700;font-size:17px;line-height:30px;padding-left:15px;white-space:nowrap}
  .contact{position:absolute;left:197px;top:976px;font-family:"Poppins",sans-serif;font-size:14.5px;line-height:17.5px;color:var(--ink);list-style:none}
  .contact li{display:flex;align-items:center;gap:6px}
  .contact svg{width:13px;height:13px;flex:none}
  .brand-mark{position:absolute;left:28px;top:900px;width:144px;height:144px;border-radius:50%;background:var(--white);box-shadow:0 2px 6px rgba(0,0,0,.18);display:flex;align-items:center;justify-content:center;text-align:center}
  .brand-name{font-weight:600;font-size:15px;line-height:19px;color:var(--brand-blue)}
</style>
</head>
<body>
<div class="flyer">
  <svg class="flyer-shapes" viewBox="0 0 1075 2278" preserveAspectRatio="none">
    <defs>
      <linearGradient id="photoTone" x1="0" y1="0" x2="1" y2="0">
        <stop offset="0" stop-color="#c9ced1"/>
        <stop offset=".55" stop-color="#e2e5e6"/>
        <stop offset="1" stop-color="#f8f9f9"/>
      </linearGradient>
      <linearGradient id="blueField" x1="0" y1="0" x2="0" y2="1">
        <stop offset="0" stop-color="#3cb8ea"/>
        <stop offset=".45" stop-color="#2a80c8"/>
        <stop offset="1" stop-color="#2366b6"/>
      </linearGradient>
      <linearGradient id="columnTone" x1="0" y1="0" x2="0" y2="1">
        <stop offset="0" stop-color="#1d63a8" stop-opacity="0"/>
        <stop offset=".25" stop-color="#1a5499"/>
        <stop offset="1" stop-color="#1b56a0"/>
      </linearGradient>
      <linearGradient id="circlePhoto" x1="0" y1="0" x2="1" y2="1">
        <stop offset="0" stop-color="#e6ecf2"/>
        <stop offset="1" stop-color="#c3ccd6"/>
      </linearGradient>
    </defs>

    <rect class="hero-photo" x="0" y="0" width="1075" height="1300" fill="url(#photoTone)" role="img" aria-label="Photo: osteopath treating a seated patient's shoulder and back"/>

    <path class="blue-field" d="M0 1240 C 300 1020 720 820 1075 450 L1075 2278 L0 2278 Z" fill="url(#blueField)"/>
    <path class="spine-band" d="M0 1160 C 280 930 700 690 1075 250" fill="none" stroke="var(--spine)" stroke-width="120" role="img" aria-label="Decorative spine graphic"/>
    <path d="M0 1300 C 330 1060 760 850 1075 520" fill="none" stroke="#9fdcf6" stroke-width="10" opacity=".8"/>

    <rect class="reasons-column" x="420" y="960" width="185" height="1100" fill="url(#columnTone)"/>

    <circle cx="347" cy="817" r="237" fill="var(--orange)"/>
    <circle cx="347" cy="817" r="205" fill="url(#circlePhoto)" role="img" aria-label="Photo: smiling practitioner holding a spine model"/>

    <g class="condition-icons" fill="none" stroke="#ffffff" stroke-width="2.5" stroke-linecap="round" stroke-linejoin="round">
      <!-- back / neck -->
      <g transform="translate(710 788)">
        <circle r="61"/>
        <path d="M-30 30 C-30 0 -26 -18 -10 -22 L10 -22 C26 -18 30 0 30 30"/>
        <circle cy="-32" r="9"/>
        <path d="M0 -20 V28 M-6 -8 H6 M-6 4 H6 M-6 16 H6"/>
      </g>
      <!-- headaches -->
      <g transform="translate(920 788)">
        <circle r="61"/>
        <path d="M-22 32 V14 C-34 4 -34 -26 -6 -32 C18 -36 32 -18 28 2 C26 14 20 18 20 32"/>
        <path d="M4 -26 L-6 -6 H6 L-4 14"/>
      </g>
      <!-- joint and muscle -->
      <g transform="translate(710 1025)">
        <circle r="61"/>
        <path d="M-30 -30 L-4 -4 M-20 -36 L4 -12"/>
        <circle cx="2" cy="-2" r="10"/>
        <path d="M0 8 L-6 36 M10 6 L10 36"/>
        <path d="M22 -24 L30 -30 M24 -14 H34"/>
      </g>
      <!-- disc -->
      <g transform="translate(920 1025)">
        <circle r="61"/>
        <rect x="-20" y="-34" width="40" height="14" rx="3"/>
        <rect x="-20" y="-10" width="40" height="14" rx="3"/>
        <rect x="-20" y="14" width="40" height="14" rx="3"/>
        <path d="M24 -2 L34 -8 M24 6 H36"/>
      </g>
      <!-- pregnancy -->
      <g transform="translate(710 1251)">
        <circle r="61"/>
        <path d="M-8 -36 C-20 -18 -18 -6 -10 2 C-22 14 -16 30 -10 36"/>
        <ellipse cx="8" cy="4" rx="16" ry="20"/>
        <circle cx="6" cy="0" r="6"/>
      </g>
      <!-- sciatica -->
      <g transform="translate(923 1259)">
        <circle r="61"/>
        <path d="M-14 -36 V36 M-14 -6 C0 4 4 16 2 36 M-14 10 C-26 18 -28 28 -26 36"/>
        <circle cx="20" cy="-4" r="11"/>
        <path d="M20 -10 V-2 M20 3 V3.5"/>
      </g>
      <!-- plantar -->
      <g transform="translate(710 1513)">
        <circle r="61"/>
        <path d="M-6 -38 C-2 -10 6 4 26 14 C34 18 34 28 24 30 L-26 30 C-34 30 -34 22 -28 18 C-18 10 -16 -10 -18 -38"/>
        <path d="M-18 22 C-4 14 6 18 14 24"/>
      </g>
      <!-- tendonitis -->
      <g transform="translate(922 1513)">
        <circle r="61"/>
        <path d="M-14 -38 V-14 M6 -38 V-14 M-18 -14 C-18 -4 10 -4 10 -14"/>
        <path d="M-18 14 C-18 4 10 4 10 14 M-14 14 V38 M6 14 V38"/>
        <path d="M18 -26 C34 -10 34 10 18 26"/>
      </g>
      <!-- adhesive capsulitis -->
      <g transform="translate(715 1741)">
        <circle r="61"/>
        <rect x="-24" y="-30" width="20" height="50" rx="10"/>
        <path d="M-24 -5 H-4"/>
        <rect x="2" y="-4" width="36" height="18" rx="9" transform="rotate(-40 20 5)"/>
        <circle cx="18" cy="-26" r="3"/><circle cx="-32" cy="28" r="3"/><circle cx="30" cy="26" r="3"/>
      </g>
      <!-- tennis / golfers elbow -->
      <g transform="translate(927 1741)">
        <circle r="61"/>
        <ellipse cx="10" cy="-22" rx="18" ry="14"/>
        <path d="M-2 -12 H22 M10 -36 V-8"/>
        <path d="M10 -8 V8"/>
        <path d="M-34 10 C-20 2 -4 4 2 8 L24 8 L24 28 L-4 28 C-14 28 -24 26 -34 24"/>
      </g>
    </g>

    <path class="footer-wave" d="M0 1975 C 260 1850 520 1960 790 2010 C 930 2035 1010 2010 1075 1985 L1075 2278 L0 2278 Z" fill="#ffffff"/>
    <path d="M0 1935 C 170 1830 330 1830 420 1900" fill="none" stroke="var(--orange)" stroke-width="14"/>
    <path d="M880 2000 C 960 1960 1020 1940 1075 1935" fill="none" stroke="var(--orange)" stroke-width="12"/>
    <path d="M0 1975 C 260 1850 520 1960 790 2010" fill="none" stroke="#e9ecef" stroke-width="18" opacity=".7"/>
  </svg>

  <div class="headline">
    <div class="headline-main">Natural Relief</div>
    <div class="headline-sub">Real Results</div>
  </div>

  <p class="intro">Osteopaths use<br>a combination of<br><strong>joint manipulation,</strong><br><strong>targeted deep</strong><br><strong>tissue massage</strong><br>and <strong>stretching</strong> to<br>improve <strong>function,</strong><br><strong>relieve pain</strong> and<br>support the body’s<br>ability to <strong>heal</strong><br><strong>itself.</strong></p>

  <h2 class="reasons-title">Common reasons<br>people visit an osteopath</h2>

  <div class="condition" style="left:331px;top:402px">Back<br>/ neck pain</div>
  <div class="condition" style="left:428px;top:402px;width:100px;margin-left:-50px">Headaches<br>/ migraines</div>
  <div class="condition" style="left:331px;top:512px">Joint and<br>muscle pain</div>
  <div class="condition" style="left:428px;top:512px">Disc related<br>issues</div>
  <div class="condition" style="left:333px;top:617px">Pregnancy<br>related<br>discomfort</div>
  <div class="condition" style="left:430px;top:628px">Sciatica</div>
  <div class="condition" style="left:330px;top:740px">Plantar<br>fasciitis</div>
  <div class="condition" style="left:430px;top:740px">Tendonitis<br>/ Bursitis</div>
  <div class="condition" style="left:332px;top:847px">Adhesive<br>capsulitis<br>(frozen<br>shoulder)</div>
  <div class="condition" style="left:431px;top:847px">Tennis<br>/ Golfers<br>elbow</div>

  <div class="brand-mark"><span class="brand-name">Brookmere<br>Osteopathy</span></div>

  <div class="call-pill">Phone number coming soon</div>
  <ul class="contact">
    <li><svg viewBox="0 0 24 24"><path d="M12 2a7 7 0 0 0-7 7c0 5 7 13 7 13s7-8 7-13a7 7 0 0 0-7-7zm0 9.5A2.5 2.5 0 1 1 12 6.5a2.5 2.5 0 0 1 0 5z" fill="#f28a2e"/></svg>48 Fernvale Road, Brookmere</li>
    <li><svg viewBox="0 0 24 24"><rect x="2.5" y="5" width="19" height="14" fill="none" stroke="#f28a2e" stroke-width="1.8"/><path d="M3 6l9 7 9-7" fill="none" stroke="#f28a2e" stroke-width="1.8"/></svg>info@brookmereosteopathy.example</li>
    <li><svg viewBox="0 0 24 24"><g fill="none" stroke="#f28a2e" stroke-width="1.6"><circle cx="12" cy="12" r="9.5"/><ellipse cx="12" cy="12" rx="4.2" ry="9.5"/><path d="M2.5 12h19M4 7h16M4 17h16"/></g></svg>www.brookmereosteopathy.example</li>
  </ul>
</div>
</body>
</html>
```